Telecommunications Company needs a business card design

We are looking for a sleek, professional and modern business card design based off our new logo. Will look at both light and dark options. On some designs please provide a small space for a QR code

Target Market(s)

B2B clients in Australia

Contact Information for Business Card

Name, Position, Brisbane (head) office, Phone number, email address, QR code (link to our website qlinetelecom.com.au

Colors
0054AA
0677BA
7BADD7
CADEEF
E8F1F8
0094D4
00A9DD
6FCCEA
C7EBF8
E9F6FB
00AB8E
00BBA5
67D7C9
C6EFE9
E9F9F6

```html
<!DOCTYPE html>
<html lang="en">
<head>
<meta charset="utf-8">
<title>Qline Telecom – Business Card</title>
<link rel="stylesheet" href="https://fonts.googleapis.com/css2?family=Montserrat:wght@400;500;700&display=swap">
<style>
  :root {
    --bg: #151515;
    --card: #232323;
    --card-edge: #1c1c1c;
    --blue-deep: #0054AA;
    --blue: #0677BA;
    --cyan: #00A9DD;
    --teal: #00BBA5;
    --grey: #9aa1a8;
    --white: #f2f2f2;
  }
  * { box-sizing: border-box; margin: 0; padding: 0; }
  html, body {
    width: 1200px; height: 900px; overflow: hidden;
    background: var(--bg);
    font-family: "Montserrat", sans-serif;
  }
  .stage {
    width: 1200px; height: 900px;
    display: flex; flex-direction: column;
    align-items: center; justify-content: center; gap: 40px;
  }
  .card {
    position: relative;
    width: 700px; height: 400px;
    background: linear-gradient(160deg, var(--card) 0%, var(--card-edge) 100%);
    border-bottom: 6px solid var(--blue);
    box-shadow: 0 18px 40px rgba(0,0,0,.55);
  }
  /* front */
  .card--front {
    display: flex; align-items: center; justify-content: center;
  }
  .brand {
    display: flex; align-items: center; gap: 16px;
    font-weight: 700; color: var(--cyan);
  }
  .brand__dot {
    width: 30px; height: 30px; border-radius: 50%;
    background: var(--teal);
  }
  .card--front .brand { font-size: 52px; letter-spacing: 1px; }
  /* back */
  .card--back {
    display: flex; align-items: center;
    padding: 0 50px 0 56px;
  }
  .card--back .brand { font-size: 40px; width: 300px; line-height: 1.05; }
  .divider {
    width: 3px; height: 170px; background: var(--cyan);
    margin: 0 30px 0 24px;
  }
  .details { color: var(--white); }
  .details__name {
    font-weight: 700; font-size: 24px; color: var(--blue);
    letter-spacing: .5px;
  }
  .details__role { font-size: 18px; margin-bottom: 16px; }
  .details__office { font-size: 17px; margin-bottom: 14px; }
  .details__list { list-style: none; font-size: 17px; line-height: 1.55; }
  .details__list li { display: flex; align-items: center; gap: 10px; }
  .icon { width: 14px; height: 14px; flex: none; }
</style>
</head>
<body>
<main class="stage">
  <section class="card card--front" aria-label="Card front">
    <div class="brand"><span class="brand__dot"></span>Qline Telecom</div>
  </section>

  <section class="card card--back" aria-label="Card back">
    <div class="brand"><span class="brand__dot"></span>Qline Telecom</div>
    <div class="divider"></div>
    <div class="details">
      <p class="details__name">MARK ELLISON</p>
      <p class="details__role">Director</p>
      <p class="details__office">Brisbane (head) office</p>
      <ul class="details__list">
        <li>
          <svg class="icon" viewBox="0 0 16 16" fill="none" stroke="#0677BA" stroke-width="1.6"><path d="M3 1.5h3l1.2 3.3-1.8 1.2a8 8 0 0 0 4.6 4.6l1.2-1.8 3.3 1.2v3c0 .6-.4 1-1 1A12.5 12.5 0 0 1 2 2.5c0-.6.4-1 1-1z"/></svg>
          (123) 456-7890
        </li>
        <li>
          <svg class="icon" viewBox="0 0 16 16" fill="none" stroke="#0677BA" stroke-width="1.6"><rect x="1.5" y="3.5" width="13" height="9"/><path d="M1.5 3.5l6.5 5 6.5-5"/></svg>
          qlinetelecom.com.au
        </li>
        <li>
          <svg class="icon" viewBox="0 0 16 16" fill="none" stroke="#0677BA" stroke-width="1.4"><circle cx="8" cy="8" r="6.5"/><ellipse cx="8" cy="8" rx="3" ry="6.5"/><path d="M1.5 8h13"/></svg>
          qlinetelecom.com.au
        </li>
      </ul>
    </div>
  </section>
</main>
</body>
</html>
```